Volbrey Inc Business Card

Looking to get an updated business card for a Contract Machining company (www.volbreyinc.example) - looking for a clean design the portrays the technical nature of the business - colors can follow the website design and be in any combination that makes sense (red black, white, metallic or silver) - logos attached for use also. Would like space for: Name, title, business phone (555 214-3086), cell phone , website (www.volbreyinc.example) - possibly QR code could be integrated for website (designer choice), business address - 418 Harlow Bend, Frankenmuth, MI 48199 (cards will be for 4 employees, I will either need to modify a template or I can provide individual information)
Target Market(s)
Aerospace, defense and medical device manufacturing companies that need machining
Industry/Entity Type
Machining for aerospace, defense, medical
Contact Information for Business Card
Name, Title, Business Phone, Cell Phone, email, business website and business address
Look and feel

```html
<!DOCTYPE html>
<html lang="en">
<head>
<meta charset="utf-8">
<title>Volbrey Inc Business Card</title>
<link href="https://fonts.googleapis.com/css2?family=Montserrat:wght@400;500;700&display=swap" rel="stylesheet">
<style>
  :root {
    --backdrop: #7a6249;
    --card-light: #ffffff;
    --card-dark: #141414;
    --brand-red: #b41c23;
    --mark-red: #bb4034;
    --ink: #1c1c1c;
  }
  * { margin: 0; padding: 0; box-sizing: border-box; }
  html, body { width: 900px; height: 1200px; overflow: hidden; }
  body {
    position: relative;
    background: var(--backdrop);
    font-family: "Montserrat", Arial, sans-serif;
    color: var(--ink);
  }
  .card {
    position: absolute;
    width: 742px;
    height: 440px;
    border-radius: 24px;
    overflow: hidden;
  }
  .card--front { left: 80px; top: 131px; background: var(--card-light); }
  .card--back { left: 79px; top: 638px; background: var(--card-dark); }

  .brand-disc {
    position: absolute;
    left: 137px; top: 139px;
    width: 200px; height: 200px;
    border-radius: 50%;
    background: var(--mark-red);
    display: flex; align-items: center; justify-content: center;
  }
  .brand-disc__name {
    color: var(--card-light);
    font-weight: 700;
    font-size: 28px;
    letter-spacing: 0.5px;
  }
  .divider {
    position: absolute;
    left: 355px; top: 131px;
    width: 2px; height: 210px;
    background: var(--brand-red);
  }
  .contact { position: absolute; left: 374px; top: 127px; }
  .contact__name {
    color: var(--brand-red);
    font-weight: 700;
    font-size: 26px;
    line-height: 32px;
  }
  .contact__title { font-size: 16px; line-height: 20px; }
  .contact__address { margin-top: 16px; font-size: 16px; line-height: 20px; }
  .contact__list { margin-top: 14px; list-style: none; }
  .contact__item {
    display: flex; align-items: center;
    font-size: 16px; line-height: 23px;
  }
  .contact__icon { width: 15px; height: 15px; margin-right: 8px; fill: var(--brand-red); }

  .back-disc {
    position: absolute;
    left: 268px; top: 58px;
    width: 248px; height: 248px;
    border-radius: 50%;
    background: var(--brand-red);
  }
  .back-name {
    position: absolute;
    left: 142px; width: 500px; top: 318px;
    text-align: center;
    color: var(--brand-red);
    font-weight: 700;
    font-size: 48px;
    letter-spacing: 1px;
  }
</style>
</head>
<body>
  <section class="card card--front">
    <div class="brand-disc"><span class="brand-disc__name">Volbrey</span></div>
    <div class="divider"></div>
    <div class="contact">
      <p class="contact__name">Dorian Vale</p>
      <p class="contact__title">Owner</p>
      <p class="contact__address">418 Harlow Bend,<br>Corran Falls, OR 48199</p>
      <ul class="contact__list">
        <li class="contact__item">
          <svg class="contact__icon" viewBox="0 0 16 16"><path d="M3.5 1l2.5 3-1.5 1.8c.9 2 2.5 3.6 4.5 4.5L10.8 8.8l3.2 2.4-1.3 3C6.8 14 2 9.2 1.8 3.3z"/></svg>
          555 214-3086
        </li>
        <li class="contact__item">
          <svg class="contact__icon" viewBox="0 0 16 16"><path d="M1 5c2-3 12-3 14 0v2h-3.5V5.5h-7V7H1z"/><path d="M3 8h10l1 6H2zm5 1.5a2 2 0 100 4 2 2 0 000-4z"/></svg>
          555 214-3086
        </li>
        <li class="contact__item">
          <svg class="contact__icon" viewBox="0 0 16 16"><path d="M1 3h14v1.2L8 9 1 4.2z"/><path d="M1 5.8l7 4.8 7-4.8V13H1z"/></svg>
          info@volbreyinc.example
        </li>
        <li class="contact__item">
          <svg class="contact__icon" viewBox="0 0 16 16"><circle cx="8" cy="8" r="7"/><path d="M4 4.5c1.5.5 2 1.5 1.5 3 1.5 0 2 1 1.8 2.5L9 13" stroke="#fff" stroke-width="1.2" fill="none"/></svg>
          www.volbreyinc.example
        </li>
      </ul>
    </div>
  </section>

  <section class="card card--back">
    <div class="back-disc"></div>
    <p class="back-name">VOLBREY</p>
  </section>
</body>
</html>
```